TEBSIRK HOA Portal Site for Public

Clean up and organize current website; need website to look good and functional; this is a HOA (homeowner association management) website where homeowners can login and pay their bill, general information about a HOA, monthly newsletter page.
Competitors:
https://quillmarsh.example/
https://dorvinpalms.example/
https://www.kelbrookhomes.example/nevada
http://www.tpw-hoa.example/

Target Market(s)

homeowners

Industry/Entity Type

Real Estate

Coding

Coded - Design and coding required

Number of Pages Required

5+ page

Font styles to use
Serif

Colors
0292cd
33a6d7
e667a6
e34297

Requirements
Must have
• login to pay
• services page
• contact us
• order resale package
Nice to have
• page why an HOA would contract us

```html
<!DOCTYPE html>
<html lang="en">
<head>
<meta charset="utf-8">
<title>TEBSIRK HOA</title>
<link href="https://fonts.googleapis.com/css2?family=Oswald:wght@400;500;600&family=Open+Sans:wght@400;600;700&display=swap" rel="stylesheet">
<style>
:root{
  --blue:#0292cd;
  --blue-light:#33a6d7;
  --pink:#e34297;
  --pink-light:#e667a6;
  --ink:#222;
  --muted:#666;
  --grey-bg:#f1f1f1;
  --dark:#161616;
  --white:#fff;
}
*{box-sizing:border-box;margin:0;padding:0}
html,body{width:1200px;height:3524px;overflow:hidden}
body{font-family:"Open Sans",Arial,sans-serif;color:var(--ink);background:var(--white);position:relative}
.head{font-family:"Oswald",Arial,sans-serif;text-transform:uppercase}

/* header */
.site-header{position:absolute;top:0;left:0;width:1200px;height:136px;display:flex;align-items:center;justify-content:space-between;padding:0 120px 0 112px}
.brand{display:flex;flex-direction:column;align-items:flex-start;gap:6px}
.brand-mark{width:40px;height:40px;background:var(--blue)}
.brand-name{font-family:"Oswald",Arial,sans-serif;font-size:15px;font-weight:500;color:var(--ink);text-transform:uppercase;letter-spacing:.5px}
.main-nav{display:flex;gap:34px}
.main-nav a{font-family:"Oswald",Arial,sans-serif;font-size:15px;color:var(--ink);text-decoration:none;text-transform:uppercase;position:relative}
.main-nav a.active{color:var(--blue)}
.main-nav a.active::after{content:"";position:absolute;left:50%;top:26px;width:0;height:0;border:7px solid transparent;border-top:9px solid var(--blue);transform:translateX(-50%)}

/* hero */
.hero{position:absolute;top:136px;left:0;width:1200px;height:668px;background:linear-gradient(180deg,#1f2c47 0%,#3d5a86 35%,#7c8a8f 60%,#3f5a2e 85%,#2b3d20 100%)}
.login-btn{position:absolute;top:24px;right:44px;background:var(--pink);color:var(--white);font-family:"Oswald",Arial,sans-serif;font-size:15px;padding:10px 26px 10px 44px;border-radius:3px;text-transform:uppercase}
.login-btn svg{position:absolute;left:18px;top:12px}
.hero-title{position:absolute;left:50%;top:396px;transform:translateX(-50%);background:rgba(2,146,205,.85);color:var(--white);font-family:"Oswald",Arial,sans-serif;font-size:44px;font-weight:500;padding:6px 30px;text-transform:uppercase;white-space:nowrap}
.hero-sub{position:absolute;left:50%;top:482px;transform:translateX(-50%);background:rgba(2,146,205,.85);color:var(--white);font-family:"Oswald",Arial,sans-serif;font-size:24px;padding:8px 22px;text-transform:uppercase;white-space:nowrap}
.hero-dots{position:absolute;left:50%;bottom:18px;transform:translateX(-50%);display:flex;gap:10px}
.hero-dots span{width:10px;height:10px;border-radius:50%;background:rgba(255,255,255,.5)}
.hero-dots span.on{background:var(--white)}

/* about */
.about{position:absolute;top:804px;left:0;width:1200px;height:586px}
.about-kicker{position:absolute;left:112px;top:110px;font-size:24px;color:var(--ink)}
.about-title{position:absolute;left:112px;top:144px;font-size:44px;color:var(--blue);font-weight:500}
.about-text{position:absolute;left:112px;top:226px;width:400px;font-size:12.5px;line-height:22px;color:var(--muted)}
.btn-blue{position:absolute;left:112px;top:470px;background:var(--blue);color:var(--white);font-family:"Oswald",Arial,sans-serif;font-size:15px;padding:11px 24px;text-transform:uppercase}
.about-badge{position:absolute;left:636px;top:80px;width:400px;height:400px;display:flex;flex-direction:column;align-items:center;justify-content:center;gap:18px}
.about-badge .sq{width:120px;height:120px;background:var(--blue)}
.about-badge .nm{font-family:"Oswald",Arial,sans-serif;font-size:40px;font-weight:500;color:var(--blue);text-transform:uppercase}

/* articles */
.articles{position:absolute;top:1390px;left:0;width:1200px;height:800px;background:var(--grey-bg)}
.section-title{position:absolute;left:0;width:1200px;text-align:center;font-size:40px;font-weight:500;color:var(--ink)}
.section-title em{font-style:normal;color:var(--blue)}
.articles .section-title{top:50px}
.articles .lede{position:absolute;top:116px;width:1200px;text-align:center;font-size:14px;color:var(--muted)}
.card{position:absolute;top:172px;width:312px;height:540px;background:var(--blue);color:var(--white);text-align:center}
.card.pink{background:var(--pink)}
.card-photo{height:244px;background:linear-gradient(135deg,#cfd6d8,#8fa1a6)}
.card.pink .card-photo{background:linear-gradient(135deg,#d9c7b6,#9c8a78)}
.card h3{font-family:"Oswald",Arial,sans-serif;font-size:19px;font-weight:500;text-transform:uppercase;line-height:26px;padding:0 24px;margin-top:26px}
.card p{font-size:12px;line-height:19px;padding:0 30px;margin-top:14px;opacity:.92}
.card .btn-outline{position:absolute;left:50%;bottom:40px;transform:translateX(-50%);border:2px solid var(--white);font-family:"Oswald",Arial,sans-serif;font-size:15px;padding:8px 22px;text-transform:uppercase}

/* testimonials */
.testimonials{position:absolute;top:2190px;left:0;width:1200px;height:486px;background:linear-gradient(90deg,rgba(2,146,205,.95),rgba(51,166,215,.85) 40%,rgba(230,103,166,.9) 70%,rgba(227,66,151,.97))}
.testimonials .section-title{top:54px;color:var(--white)}
.quote{position:absolute;top:168px;width:300px;text-align:center;color:var(--white)}
.quote .ring{width:66px;height:66px;border:2px solid var(--white);border-radius:50%;margin:0 auto;display:flex;align-items:center;justify-content:center;font-family:Georgia,serif;font-size:44px;line-height:1;padding-top:16px}
.quote p{font-size:11.5px;line-height:18px;margin-top:30px;padding:0 30px}
.quote .who{font-family:"Oswald",Arial,sans-serif;font-size:14px;margin-top:20px;text-transform:uppercase}
.quote .role{font-size:11px;opacity:.85;margin-top:2px}

/* contact */
.contact{position:absolute;top:2676px;left:0;width:1200px;height:450px}
.contact .section-title{top:46px}
.map{position:absolute;left:154px;top:146px;width:400px;height:240px;background:linear-gradient(135deg,#e7e4dc,#d4dcd0)}
.address{position:absolute;left:588px;top:150px;font-size:12px;line-height:21px;color:var(--muted)}
.form{position:absolute;left:588px;top:232px;width:462px;height:186px}
.field{position:absolute;border:1px solid #d2d2d2;font-size:12px;color:#888;padding:7px 10px;height:34px;width:214px}
.field.msg{height:122px;left:240px;top:0}
.btn-pink{position:absolute;left:0;top:144px;background:var(--pink);color:var(--white);font-family:"Oswald",Arial,sans-serif;font-size:15px;padding:8px 24px;text-transform:uppercase}

/* footer */
.site-footer{position:absolute;top:3126px;left:0;width:1200px;height:398px;background:var(--dark);color:var(--white)}
.news{position:absolute;left:154px;top:60px;display:flex;align-items:center;gap:24px}
.news .lbl{font-family:"Oswald",Arial,sans-serif;font-size:30px;text-transform:uppercase}
.news .inp{width:560px;height:46px;background:var(--white);display:flex;align-items:center;justify-content:space-between;padding-left:16px;font-size:13px;color:#999}
.news .go{width:46px;height:46px;background:var(--pink);display:flex;align-items:center;justify-content:center}
.footer-rule{position:absolute;left:0;top:148px;width:1200px;height:1px;background:#333}
.footer-brand{position:absolute;left:154px;top:190px;display:flex;flex-direction:column;align-items:center;gap:8px}
.footer-brand .brand-name{color:var(--white)}
.footer-nav{position:absolute;left:512px;top:200px;display:flex;gap:34px}
.footer-nav a{font-family:"Oswald",Arial,sans-serif;font-size:14px;color:var(--white);text-decoration:none;text-transform:uppercase}
.copy{position:absolute;left:512px;top:272px;font-size:12px;color:#bbb}
.social{position:absolute;left:852px;top:262px;display:flex;gap:10px}
.social span{width:34px;height:34px;border:1.5px solid var(--white);border-radius:50%}
</style>
</head>
<body>

<header class="site-header">
  <div class="brand">
    <div class="brand-mark"></div>
    <div class="brand-name">Ridgeline Association Management</div>
  </div>
  <nav class="main-nav">
    <a class="active" href="#">Home</a>
    <a href="#">About</a>
    <a href="#">Partner With Us</a>
    <a href="#">Elements of Living</a>
    <a href="#">Contact Us</a>
  </nav>
</header>

<section class="hero" role="img" aria-label="Photo of a lit two-storey family home at dusk with a green front lawn">
  <div class="login-btn"><svg width="16" height="16" viewBox="0 0 16 16"><circle cx="8" cy="5" r="3.5" fill="#fff"/><path d="M1 16c0-4 3-6 7-6s7 2 7 6z" fill="#fff"/></svg>Resident Login</div>
  <div class="hero-title">TEBSIRK HOA</div>
  <div class="hero-sub">Sed ut perspiciatis unde omnis iste natus error sit voluptatem</div>
  <div class="hero-dots"><span class="on"></span><span></span><span></span></div>
</section>

<section class="about">
  <div class="about-kicker head">About Our</div>
  <h2 class="about-title head">TEBSIRK HOA</h2>
  <p class="about-text">Our mission each day is to deliver exceptional service and solutions that enhance the value of every property and the lifestyle of every resident in our care. By developing forward-thinking offerings, Kelbrook Homes has raised the bar for quality and service excellence. Across every day-to-day task we care for residents and boards. Our wide range of solutions are backed by local teams that put you first in all our work. Communities managed by Kelbrook Homes gain exclusive use of our advanced, proprietary technology, as well as our 24/7 care center.</p>
  <div class="btn-blue">Read More</div>
  <div class="about-badge"><div class="sq"></div><div class="nm">TEBSIRK HOA</div></div>
</section>

<section class="articles">
  <h2 class="section-title head">Latest <em>Articles</em></h2>
  <p class="lede">We are Ridgeline Association Management, a leading residential property management company in Nevada dedicated</p>

  <article class="card" style="left:112px">
    <div class="card-photo" role="img" aria-label="Photo of an older couple relaxing at home"></div>
    <h3>Aging Gracefully: The Retirement Industry in South Florida</h3>
    <p>Florida's population of residents 65 years old and over is the largest in the nation, and the state keeps growing with many new homes.</p>
    <div class="btn-outline">Read More</div>
  </article>

  <article class="card pink" style="left:444px">
    <div class="card-photo" role="img" aria-label="Photo of an older group sharing a meal outdoors"></div>
    <h3>Elderly New Yorkers, Here for the Duration</h3>
    <p>While many older New Yorkers head south to settle for their sunset years, a growing number of city residents are staying right where they are.</p>
    <div class="btn-outline">Read More</div>
  </article>

  <article class="card" style="left:776px">
    <div class="card-photo" role="img" aria-label="Photo of a smiling couple in a living room"></div>
    <h3>How to Apply the Right Criteria to Evaluate Property Management Companies</h3>
    <p>The homeowners in your association depend on you and other board members to hire a thorough, honest and competent team.</p>
    <div class="btn-outline">Read More</div>
  </article>
</section>

<section class="testimonials" aria-label="Client testimonials over a faded photo of a group of people">
  <h2 class="section-title head">What Our Clients Saying</h2>
  <div class="quote" style="left:132px">
    <div class="ring">&ldquo;</div>
    <p>Sed ut perspiciatis unde omnis iste natus error sit voluptatem accusantium doloremque laudantium, totam rem aperiam.</p>
    <div class="who">Dana Hollis</div><div class="role">President, Willow Crest HOA</div>
  </div>
  <div class="quote" style="left:450px">
    <div class="ring">&ldquo;</div>
    <p>Sed ut perspiciatis unde omnis iste natus error sit voluptatem accusantium doloremque laudantium, totam rem aperiam.</p>
    <div class="who">Dana Hollis</div><div class="role">President, Willow Crest HOA</div>
  </div>
  <div class="quote" style="left:768px">
    <div class="ring">&ldquo;</div>
    <p>Sed ut perspiciatis unde omnis iste natus error sit voluptatem accusantium doloremque laudantium, totam rem aperiam.</p>
    <div class="who">Dana Hollis</div><div class="role">President, Willow Crest HOA</div>
  </div>
</section>

<section class="contact">
  <h2 class="section-title head">Contact <em>Us</em></h2>
  <div class="map" role="img" aria-label="Street map of the service area with office location pins"></div>
  <div class="address">Address: 1420 Larkspur Avenue, Suite 210<br>Henderson, NV 89052<br>Phone: (702) 555-0148</div>
  <div class="form">
    <div class="field" style="left:0;top:0">Name</div>
    <div class="field" style="left:0;top:44px">Email</div>
    <div class="field" style="left:0;top:88px">Phone</div>
    <div class="field msg">Message</div>
    <div class="btn-pink">Submit</div>
  </div>
</section>

<footer class="site-footer">
  <div class="news">
    <div class="lbl">Newsletter Sign Up :</div>
    <div class="inp">Enter Your Email<div class="go"><svg width="18" height="18" viewBox="0 0 18 18"><path d="M1 9l16-7-6 15-2-6z" fill="#fff"/></svg></div></div>
  </div>
  <div class="footer-rule"></div>
  <div class="footer-brand">
    <div class="brand-mark"></div>
    <div class="brand-name">Ridgeline Association Management</div>
  </div>
  <nav class="footer-nav">
    <a href="#">Home</a><a href="#">About</a><a href="#">Partner With Us</a><a href="#">Elements of Living</a><a href="#">Contact Us</a>
  </nav>
  <div class="copy">&copy; Copyright 2019 Tebsirk HOA. All rights reserved.</div>
  <div class="social"><span></span><span></span><span></span><span></span><span></span></div>
</footer>

</body>
</html>
```